Specialised investor in e-mobility and energy wants business card design

We need a business card design that fits our existing corporate design. <The look and feel must be 'sharp'/'clean', dynamic, communicate momentum, professionalism etc (as one would imagine from a firm in the financial sector). We like the idea of a reverse-side of the card that includes the logo, and the name and contact details on the other. We expect the deliverable to be whatever format might be required to be able to get cards printed directly by a service such as kelmo press. Our website is www.zub.capital

```html
<!DOCTYPE html>
<html lang="en">
<head>
<meta charset="utf-8">
<title>ZUB Capital – Business Card</title>
<link rel="stylesheet" href="https://fonts.googleapis.com/css2?family=Montserrat:wght@400;500;700&display=swap">
<style>
  :root {
    --backdrop: #dcdcda;
    --paper: #ffffff;
    --brand-green: #88b04b;
    --brand-dark: #325024;
    --ink: #2b2b2b;
  }
  * { box-sizing: border-box; margin: 0; padding: 0; }
  html, body { width: 1200px; height: 801px; overflow: hidden; }
  body {
    background: var(--backdrop);
    font-family: "Montserrat", sans-serif;
    display: flex;
    align-items: center;
    justify-content: center;
    gap: 40px;
  }
  .card {
    position: relative;
    width: 525px;
    height: 300px;
    overflow: hidden;
    box-shadow: 0 6px 18px rgba(0,0,0,0.18);
  }
  /* Front side */
  .card--front { background: var(--paper); }
  .card__swoosh { position: absolute; inset: 0; width: 100%; height: 100%; }
  .brand {
    position: absolute;
    display: flex;
    align-items: center;
    gap: 8px;
    font-weight: 500;
    white-space: nowrap;
  }
  .brand__dot { border-radius: 50%; flex: none; }
  .card--front .brand { left: 30px; top: 116px; font-size: 25px; color: var(--brand-dark); }
  .card--front .brand__dot { width: 12px; height: 12px; background: var(--brand-dark); }
  .divider {
    position: absolute;
    left: 240px; top: 28px;
    width: 1px; height: 160px;
    background: var(--brand-green);
  }
  .contact { position: absolute; left: 260px; top: 30px; color: var(--ink); }
  .contact__name {
    font-weight: 700; font-size: 17px; letter-spacing: 0.5px;
    color: var(--brand-green); text-transform: uppercase;
  }
  .contact__role { font-size: 12.5px; margin-top: 2px; }
  .contact__list { list-style: none; margin-top: 14px; font-size: 12.5px; line-height: 1.35; }
  .contact__list li { display: flex; align-items: center; gap: 8px; }
  .contact__list svg { width: 11px; height: 11px; fill: var(--brand-green); flex: none; }
  .contact__company { margin-top: 14px; font-size: 12.5px; line-height: 1.35; }
  .contact__company strong { font-weight: 400; color: var(--brand-green); display: block; }
  /* Back side */
  .card--back { background: var(--brand-green); }
  .card--back .brand {
    left: 0; right: 0; top: 0; bottom: 0;
    justify-content: center;
    font-size: 54px; color: var(--paper);
  }
  .card--back .brand__dot { width: 22px; height: 22px; background: var(--paper); }
</style>
</head>
<body>
  <section class="card card--front" aria-label="Business card front">
    <svg class="card__swoosh" viewBox="0 0 525 300" preserveAspectRatio="none" aria-hidden="true">
      <path d="M150 300 C 260 235, 400 185, 525 130 L 525 300 Z" fill="var(--brand-dark)"/>
      <path d="M190 300 C 290 245, 410 198, 525 156 L 525 300 Z" fill="var(--paper)"/>
      <path d="M202 300 C 300 249, 415 203, 525 164 L 525 300 Z" fill="var(--brand-green)"/>
      <path d="M214 300 C 310 255, 420 210, 525 173 L 525 300 Z" fill="var(--paper)"/>
      <path d="M228 300 C 320 261, 425 217, 525 182 L 525 300 Z" fill="var(--brand-dark)"/>
    </svg>
    <div class="brand"><span class="brand__dot"></span>ZUB Capital</div>
    <div class="divider"></div>
    <div class="contact">
      <p class="contact__name">Mark Ellery</p>
      <p class="contact__role">Managing Director</p>
      <ul class="contact__list">
        <li><svg viewBox="0 0 16 16"><path d="M3 1h3l1.5 4-2 1.3a9 9 0 0 0 4.2 4.2L11 8.5l4 1.5v3a2 2 0 0 1-2 2A13 13 0 0 1 1 3a2 2 0 0 1 2-2z"/></svg>+41 79555 0148</li>
        <li><svg viewBox="0 0 16 16"><path d="M1 3h14v10H1z"/><path d="M1.5 3.5 8 9l6.5-5.5" fill="none" stroke="#fff" stroke-width="1.4"/></svg>mark@zub.capital</li>
        <li><svg viewBox="0 0 16 16"><circle cx="8" cy="8" r="7"/><path d="M1 8h14M8 1c-3 4-3 10 0 14M8 1c3 4 3 10 0 14" fill="none" stroke="#fff" stroke-width="1"/></svg>www.zub.capital</li>
      </ul>
      <p class="contact__company"><strong>ZUB Capital S.A.</strong>Geneva, Switzerland</p>
    </div>
  </section>

  <section class="card card--back" aria-label="Business card back">
    <div class="brand"><span class="brand__dot"></span>ZUB Capital</div>
  </section>
</body>
</html>
```